Business Card Design

We need a design for business cards for our company. We have a logo. We teach EMT's and we are based out of Virginia. The information that will need to add would be, name, title, phone number, email, address. On the back of the business card would be "We help you, help others"

Target Market(s)

People that want to become EMT's

Colors

Designer to choose colors to be used in the design.

Requirements
Must have
• company logo

```html
<!DOCTYPE html>
<html lang="en">
<head>
<meta charset="utf-8">
<title>Medic Path Training – Business Card</title>
<link rel="stylesheet" href="https://fonts.googleapis.com/css2?family=Montserrat:wght@500;600;700&family=Arimo:wght@400&display=swap">
<style>
  :root {
    --page-bg: #d9d3cc;
    --card-top: #ecebea;
    --card-top-edge: #d8d6d5;
    --brand-red: #9e1a22;
    --band-red: #8a1119;
    --band-red-dark: #6b0b12;
    --card-dark: #25282d;
    --card-darker: #16181b;
    --name-ink: #e2d9d6;
    --contact-ink: #d4cfcd;
    --address-ink: #c9bca8;
    --icon-ink: #bfbcba;
  }
  * { margin: 0; padding: 0; box-sizing: border-box; }
  html, body { width: 1200px; height: 970px; overflow: hidden; }
  body {
    background: var(--page-bg);
    position: relative;
    font-family: "Arimo", Arial, sans-serif;
  }
  .business-card {
    position: absolute;
    left: 100px; top: 199px;
    width: 1000px; height: 572px;
    border-radius: 26px;
    overflow: hidden;
    background: linear-gradient(160deg, var(--card-top) 0%, var(--card-top-edge) 100%);
    box-shadow: 0 14px 40px rgba(0,0,0,0.25);
  }
  .brand {
    position: absolute;
    left: 64px; top: 100px;
    display: flex; align-items: center; gap: 18px;
  }
  .brand-dot {
    width: 46px; height: 46px; border-radius: 50%;
    background: var(--brand-red);
    flex: none;
  }
  .brand-name {
    font-family: "Montserrat", Arial, sans-serif;
    font-weight: 700;
    font-size: 56px;
    letter-spacing: -0.5px;
    color: var(--brand-red);
    text-transform: uppercase;
    white-space: nowrap;
  }
  .name-band {
    position: absolute;
    left: 0; top: 296px;
    width: 100%; height: 66px;
    background: linear-gradient(90deg, var(--band-red) 0%, #a31c24 45%, var(--band-red-dark) 100%);
    display: flex; align-items: center;
    padding-left: 64px;
  }
  .person-name {
    font-family: "Montserrat", Arial, sans-serif;
    font-weight: 600;
    font-size: 30px;
    color: var(--name-ink);
    text-transform: uppercase;
    white-space: nowrap;
  }
  .divider {
    width: 2px; height: 30px;
    background: var(--name-ink);
    margin: 0 16px 0 18px;
  }
  .person-title {
    font-size: 23px;
    color: var(--name-ink);
    white-space: nowrap;
  }
  .contact-panel {
    position: absolute;
    left: 0; top: 362px;
    width: 100%; height: 210px;
    background: radial-gradient(ellipse at 30% 30%, #34373c 0%, var(--card-dark) 45%, var(--card-darker) 100%);
  }
  .contact-list {
    position: absolute;
    left: 62px; top: 60px;
    list-style: none;
  }
  .contact-item {
    display: flex; align-items: center;
    height: 36px;
    font-size: 23px;
    color: var(--contact-ink);
    white-space: nowrap;
  }
  .contact-icon {
    width: 22px; height: 22px;
    margin-right: 22px;
    flex: none;
  }
  .mailing-address {
    position: absolute;
    right: 55px; top: 96px;
    text-align: right;
    font-size: 23px;
    font-style: normal;
    line-height: 36px;
    color: var(--address-ink);
    white-space: nowrap;
  }
</style>
</head>
<body>
  <section class="business-card">
    <div class="brand">
      <span class="brand-dot"></span>
      <span class="brand-name">Medic Path Training</span>
    </div>

    <div class="name-band">
      <span class="person-name">Daniel R. Hayes</span>
      <span class="divider"></span>
      <span class="person-title">Managing Director</span>
    </div>

    <div class="contact-panel">
      <ul class="contact-list">
        <li class="contact-item">
          <svg class="contact-icon" viewBox="0 0 22 22" aria-hidden="true">
            <rect x="5" y="1.5" width="12" height="19" rx="2" fill="none" stroke="var(--icon-ink)" stroke-width="2"/>
            <line x1="9" y1="17" x2="13" y2="17" stroke="var(--icon-ink)" stroke-width="2"/>
          </svg>
          +00 000 00000000
        </li>
        <li class="contact-item">
          <svg class="contact-icon" viewBox="0 0 22 22" aria-hidden="true">
            <rect x="1.5" y="4.5" width="19" height="13" fill="none" stroke="var(--icon-ink)" stroke-width="2"/>
            <polyline points="1.5,4.5 11,12 20.5,4.5" fill="none" stroke="var(--icon-ink)" stroke-width="2"/>
            <line x1="1.5" y1="17.5" x2="8.5" y2="10" stroke="var(--icon-ink)" stroke-width="1.6"/>
            <line x1="20.5" y1="17.5" x2="13.5" y2="10" stroke="var(--icon-ink)" stroke-width="1.6"/>
          </svg>
          info@medicpathtraining.com
        </li>
        <li class="contact-item">
          <svg class="contact-icon" viewBox="0 0 22 22" aria-hidden="true">
            <circle cx="11" cy="11" r="9.5" fill="none" stroke="var(--icon-ink)" stroke-width="1.6"/>
            <ellipse cx="11" cy="11" rx="4" ry="9.5" fill="none" stroke="var(--icon-ink)" stroke-width="1.4"/>
            <line x1="1.5" y1="11" x2="20.5" y2="11" stroke="var(--icon-ink)" stroke-width="1.4"/>
            <line x1="3" y1="6.5" x2="19" y2="6.5" stroke="var(--icon-ink)" stroke-width="1.2"/>
            <line x1="3" y1="15.5" x2="19" y2="15.5" stroke="var(--icon-ink)" stroke-width="1.2"/>
          </svg>
          www.medicpathtraining.com
        </li>
      </ul>

      <address class="mailing-address">
        PO BOX 418, Linden Avenue<br>
        5th street, Roanoke
      </address>
    </div>
  </section>
</body>
</html>
```